KTWG application splash screen

We need a 1024x768 image for use as an application splash screen.
The image will be displayed full screen on an 10 inch industrial PC 1024x768 screen while our application is launching. The image should convey that the application is "Waiting for connection to Wi-Fi access point..." and include a graphic of the industrial PC connected to the access point via an Ethernet cable. A list of troubleshooting steps should be included at the bottom of the image. The troubleshooting steps should not be the main focus of the image and should be shown in a smaller font (but still readable at 1024x768 displayed on a 10 inch screen).
I will include a mock up of the general idea of what we are looking for as well as image files for the industrial PC, a screenshot of our application to show on the PC's screen and the AP.
For general look and feel and a sense of corporate branding please review our website https://marrowgatesoilworks.example/. The splash screen should reflect corporate branding.
Target Market(s)
Users of our application
Industry/Entity Type
Agriculture
Look and feel

```html
<!DOCTYPE html>
<html lang="en">
<head>
<meta charset="utf-8">
<title>KTWG – Waiting for Wi-Fi</title>
<link href="https://fonts.googleapis.com/css2?family=Barlow:wght@400;500;600&display=swap" rel="stylesheet">
<style>
  :root {
    --brand-green: #2cb673;
    --brand-green-soft: #dff3e8;
    --paper: #ffffff;
    --cable: #1b1b1b;
    --device-dark: #2a2a2a;
    --device-screen: #cfe9d9;
    --ap-white: #f1f3f2;
    --ap-shade: #d9dddb;
  }
  html, body {
    margin: 0;
    padding: 0;
    width: 1200px;
    height: 900px;
    overflow: hidden;
    background: var(--brand-green);
    font-family: "Barlow", Arial, sans-serif;
  }
  .splash {
    position: relative;
    width: 1024px;
    height: 768px;
    transform: scale(1.171875);
    transform-origin: 0 0;
    background: var(--brand-green);
    color: var(--paper);
    overflow: hidden;
  }
  .backdrop {
    position: absolute;
    inset: 0;
  }
  .headline {
    position: absolute;
    left: 40px;
    top: 62px;
    width: 670px;
    margin: 0;
    text-align: center;
    font-weight: 500;
    font-size: 63px;
    line-height: 71px;
    letter-spacing: 0.5px;
  }
  .device-cab-computer {
    position: absolute;
    left: 78px;
    top: 330px;
    width: 272px;
    height: 210px;
    border-radius: 14px;
    background: linear-gradient(160deg, var(--device-dark), #141414);
  }
  .device-cab-computer::after {
    content: "";
    position: absolute;
    left: 22px;
    top: 18px;
    right: 22px;
    bottom: 26px;
    border-radius: 3px;
    background: linear-gradient(180deg, #f4f7f5, var(--device-screen));
  }
  .device-access-point {
    position: absolute;
    left: 878px;
    top: 45px;
    width: 62px;
    height: 405px;
    border-radius: 16px 16px 26px 26px;
    background: linear-gradient(90deg, var(--ap-shade), var(--ap-white) 45%, var(--ap-shade));
  }
  .label {
    position: absolute;
    margin: 0;
    font-weight: 500;
    text-align: center;
  }
  .label--computer {
    left: 100px;
    top: 551px;
    width: 222px;
    font-size: 18px;
    color: var(--brand-green);
  }
  .label--ap {
    left: 820px;
    top: 525px;
    width: 168px;
    font-size: 19px;
    line-height: 23px;
    color: var(--paper);
    letter-spacing: 0.3px;
  }
  .troubleshooting {
    position: absolute;
    left: 55px;
    top: 609px;
    width: 760px;
    font-size: 12.4px;
    line-height: 16px;
  }
  .troubleshooting h2 {
    margin: 0 0 9px;
    font-size: 13px;
    font-weight: 600;
  }
  .steps, .sub-steps {
    list-style: none;
    margin: 0;
    padding: 0;
  }
  .steps > li {
    position: relative;
    padding-left: 18px;
  }
  .steps > li::before {
    content: "➤";
    position: absolute;
    left: 0;
    top: 0;
  }
  .sub-steps li {
    position: relative;
    padding-left: 15px;
  }
  .sub-steps li::before {
    content: "➡";
    position: absolute;
    left: 0;
    top: 0;
    font-size: 11px;
  }
  .brand-mark {
    position: absolute;
    left: 840px;
    top: 648px;
    width: 140px;
    display: flex;
    align-items: center;
    gap: 10px;
    font-weight: 600;
    font-size: 36px;
    letter-spacing: 1px;
    color: var(--paper);
  }
  .brand-mark .dot {
    width: 16px;
    height: 16px;
    border-radius: 50%;
    background: var(--paper);
  }
</style>
</head>
<body>
<main class="splash">
  <svg class="backdrop" width="1024" height="768" viewBox="0 0 1024 768" aria-hidden="true">
    <path class="wave-white" fill="#ffffff"
      d="M0,380 C120,345 250,425 420,412 C590,400 690,312 788,300 L788,595 L0,595 Z"/>
    <path class="wave-soft" fill="var(--brand-green-soft)"
      d="M788,300 C870,286 960,282 1024,292 L1024,302 C960,294 870,298 788,312 Z"/>
    <path class="ethernet-cable" fill="none" stroke="var(--cable)" stroke-width="5" stroke-linecap="round"
      d="M350,487 L872,487 Q906,487 906,455 L906,446"/>
  </svg>

  <h1 class="headline">Waiting for<br>connection to Wi-Fi<br>access point...</h1>

  <div class="device-cab-computer" role="img" aria-label="Industrial tractor cab computer showing the seeding application screen"></div>
  <div class="device-access-point" role="img" aria-label="Outdoor Wi-Fi access point with two antennas"></div>

  <p class="label label--computer">Tractor Cab Computer</p>
  <p class="label label--ap">Wi-Fi Access<br>Point</p>

  <section class="troubleshooting">
    <h2>Troubleshooting steps:</h2>
    <ul class="steps">
      <li>This screen should only be visible for a short time on boot.</li>
      <li>If this screen stays visible for more than a minute:
        <ul class="sub-steps">
          <li>Verify that the Wi-Fi Access Point (AP) powers up when this system does (indicated by a green light on the side of the AP).</li>
          <li>Check the Ethernet cable between this system and the AP for damage, and replace it if necessary.</li>
          <li>Power-cycle this system and wait for it to reboot fully.</li>
          <li>If the issue persists, contact KTWG support for further assistance.</li>
        </ul>
      </li>
    </ul>
  </section>

  <div class="brand-mark"><span class="dot"></span>KTWG</div>
</main>
</body>
</html>
```